Vantro cards

I am in the auto motive, transportation business I would like a business card that is Something cool, modern edgy, having to do with car culture. I offer towing service for high and exotic cars. I also provide towing for collisions and car accidents. I offer open and enclosed transport nationwide.

Target Market(s)

Car culture people high end auto collectors

Industry/Entity Type

Towing car carrier

Contact Information for Business Card

My company colors black yellow and silver

Font styles to use
Serif

```html
<!DOCTYPE html>
<html lang="en">
<head>
<meta charset="utf-8">
<title>Vantro Transportation – Business Cards</title>
<link rel="stylesheet" href="https://fonts.googleapis.com/css2?family=Montserrat:wght@400;500;600;800&display=swap">
<style>
  :root {
    --backdrop: #857058;
    --card-white: #ffffff;
    --brand-yellow: #f7dc4a;
    --brand-black: #0c0c0c;
    --navy-ink: #1f2340;
    --text-dark: #1a1a1a;
    --rule: #1a1a1a;
    --ghost: #ececec;
    --silver-light: #f4f4f4;
    --silver-mid: #c9c9c9;
    --silver-dark: #8f8f8f;
  }
  * { margin: 0; padding: 0; box-sizing: border-box; }
  html, body { width: 900px; height: 1200px; overflow: hidden; }
  body {
    background: var(--backdrop);
    font-family: "Montserrat", Arial, sans-serif;
    position: relative;
  }
  .card {
    position: absolute;
    left: 80px;
    width: 742px;
    border-radius: 30px;
    overflow: hidden;
    box-shadow: 0 8px 18px rgba(0,0,0,0.35);
  }
  /* ---------- Front ---------- */
  .card-front { top: 132px; height: 443px; background: var(--card-white); }
  .ghost-mark {
    position: absolute; right: -20px; top: 120px;
    font-size: 130px; font-weight: 800; color: var(--ghost);
    letter-spacing: 2px; line-height: 1;
  }
  .brand-lockup {
    position: absolute; left: 36px; top: 70px;
    display: flex; align-items: center; gap: 10px;
    color: var(--brand-black); font-weight: 800;
  }
  .brand-square { width: 22px; height: 22px; background: var(--brand-yellow); }
  .brand-name { font-size: 40px; line-height: 1; letter-spacing: 1px; }
  .brand-sub {
    position: absolute; left: 36px; top: 118px;
    font-size: 17px; font-weight: 800; letter-spacing: 1.5px; color: var(--brand-black);
  }
  .person-name {
    position: absolute; left: 35px; top: 256px;
    font-size: 27px; font-weight: 600; color: var(--brand-yellow);
  }
  .person-role {
    position: absolute; left: 34px; top: 289px;
    font-size: 16px; color: var(--navy-ink);
  }
  .divider {
    position: absolute; left: 33px; top: 314px; width: 677px; height: 2px;
    background: var(--rule);
  }
  .contact-list {
    position: absolute; left: 34px; top: 326px; list-style: none;
    font-size: 16.5px; color: var(--text-dark); line-height: 21px;
  }
  .contact-list li { display: flex; align-items: center; gap: 10px; }
  .contact-list svg { width: 15px; height: 15px; fill: var(--text-dark); }
  .address {
    position: absolute; left: 530px; top: 348px;
    font-size: 16.5px; color: var(--text-dark); line-height: 21px;
  }
  .front-base { position: absolute; left: 0; bottom: 0; width: 742px; height: 45px; }

  /* ---------- Back ---------- */
  .card-back {
    top: 640px; height: 440px;
    background:
      conic-gradient(from 20deg at 50% 40%,
        var(--silver-light), var(--silver-dark), var(--silver-light),
        var(--silver-mid), var(--silver-light), var(--silver-dark),
        var(--silver-light), var(--silver-mid), var(--silver-light));
  }
  .back-lockup {
    position: absolute; left: 0; right: 0; top: 175px;
    text-align: center; color: var(--brand-black); font-weight: 800;
  }
  .back-lockup .row { display: inline-flex; align-items: center; gap: 14px; }
  .back-lockup .brand-square { width: 30px; height: 30px; }
  .back-lockup .brand-name { font-size: 62px; }
  .back-lockup .brand-sub { position: static; font-size: 22px; letter-spacing: 3px; margin-top: 8px; }
  .back-stripe {
    position: absolute; left: 0; top: 362px; width: 100%; height: 6px;
    background: var(--brand-yellow);
  }
  .back-band {
    position: absolute; left: 0; top: 380px; width: 100%; height: 60px;
    background: var(--brand-black); color: var(--card-white);
    display: flex; align-items: center; justify-content: center;
    font-size: 16px; letter-spacing: 0.3px;
  }
</style>
</head>
<body>

<section class="card card-front">
  <div class="ghost-mark" aria-hidden="true">Vantro</div>

  <div class="brand-lockup">
    <span class="brand-square"></span>
    <span class="brand-name">VANTRO</span>
  </div>
  <div class="brand-sub">TRANSPORTATION</div>

  <h1 class="person-name">Daniel Reyes</h1>
  <p class="person-role">Owner</p>
  <div class="divider"></div>

  <ul class="contact-list">
    <li>
      <svg viewBox="0 0 16 16" aria-hidden="true"><path d="M1 5c0-2 3-3 7-3s7 1 7 3v1.5h-3.5V5h-7v1.5H1zM3 8h10l1 6H2z"/></svg>
      (555) 014-2280
    </li>
    <li>
      <svg viewBox="0 0 16 16" aria-hidden="true"><path d="M1 3h14v10H1zM2 4.5v.3l6 4 6-4v-.3z"/></svg>
      info@vantrotransportation.com
    </li>
    <li>
      <svg viewBox="0 0 16 16" aria-hidden="true"><circle cx="8" cy="8" r="7"/><path d="M4 5c2 0 2 3 4 3s1 4 3 4M9 2c0 2 3 2 4 4" stroke="#fff" stroke-width="1.4" fill="none"/></svg>
      www.vantrotransportation.com
    </li>
  </ul>

  <address class="address" style="font-style:normal">48 Harbor Road<br>Millbrook, PA 17000</address>

  <svg class="front-base" viewBox="0 0 742 45" preserveAspectRatio="none" aria-hidden="true">
    <rect x="0" y="12" width="432" height="7" fill="var(--brand-yellow)"/>
    <path d="M0 19 H420 Q440 19 450 10 Q460 2 480 2 H742 V45 H0 Z" fill="var(--brand-black)"/>
    <path d="M0 19 H420 Q440 19 450 10" fill="none" stroke="var(--card-white)" stroke-width="4"/>
  </svg>
</section>

<section class="card card-back">
  <div class="back-lockup">
    <div class="row">
      <span class="brand-square"></span>
      <span class="brand-name">VANTRO</span>
    </div>
    <div class="brand-sub">TRANSPORTATION</div>
  </div>
  <div class="back-stripe"></div>
  <div class="back-band">www.vantrotransportation.com</div>
</section>

</body>
</html>
```